Sales Proposal Template Design

I sell Internet Marketing services; including search engine optimization, search engine marketing, social media, websites, mobile websites, email and video.

I produce a proposal for each prospective client. Some include SEO and PPC. Other include more services or less services. The purpose of this project is to create a template in MS Word or Power Point. I will add standard content for each product with different pricing for different projects.

I want one page for each product or service I will be presenting the the proposal. I can then use just one page or multiple pages to build the full proposal.

Once I am finished I will convert the single sheets into a PDF document to print or send to the client via email.

I am part of a the This is a KVO Franchise http://www.kvoglobe-example.com/ you can see the corporate colors and design on this website.

I would like both a vertical and horizontal orientation template.

Target Market(s)

Prospects and buyers that request information and pricing.

Industry/Entity Type

Internet

Requirements
Must have
• Must have the KVO logo and be consistent with their colors and design feel.

I need a lot of open space for content copy.

The template needs to be in MS Word or Power Point.
Nice to have
• A front cover design that matches the inside page template would be nice to have.

```html
<!DOCTYPE html>
<html lang="en">
<head>
<meta charset="utf-8">
<title>Proposal Page – Subheading</title>
<link rel="stylesheet" href="https://fonts.googleapis.com/css2?family=Open+Sans:wght@300;400&family=Questrial&display=swap">
<style>
  :root {
    --canvas: #ffffff;
    --navy: #0a2f63;
    --blue-deep: #0d5aa6;
    --blue-mid: #1e86d0;
    --blue-light: #7fd0f3;
    --panel: rgba(20, 80, 150, 0.55);
    --text: #ffffff;
    --ribbon-red: #c0412a;
    --ribbon-blue: #1670bb;
    --ground: #ffffff;
    --globe-light: #e6f3fb;
    --globe-mid: #8cc3e6;
    --globe-deep: #2f7fc1;
  }
  * { margin: 0; padding: 0; box-sizing: border-box; }
  html, body { width: 1200px; height: 900px; overflow: hidden; background: var(--canvas); }
  .canvas { position: relative; width: 1200px; height: 900px; }
  .page {
    position: absolute; left: 133px; top: 101px; width: 933px; height: 697px;
    overflow: hidden;
    background: radial-gradient(ellipse 620px 520px at 470px 470px, var(--blue-light) 0%, var(--blue-mid) 38%, var(--blue-deep) 70%, var(--navy) 100%);
    box-shadow: 6px 8px 10px rgba(0, 0, 0, 0.35);
  }
  .wave-artwork {
    position: absolute; left: 0; top: 478px; width: 933px; height: 219px;
    background: linear-gradient(to bottom,
      rgba(30, 134, 208, 0) 0%,
      rgba(22, 112, 187, 0.85) 30%,
      rgba(156, 201, 234, 0.9) 55%,
      var(--ground) 78%);
  }
  .globe-artwork {
    position: absolute; left: 617px; top: 438px; width: 187px; height: 187px; border-radius: 50%;
    background: radial-gradient(circle at 40% 35%, var(--globe-light) 0%, var(--globe-mid) 55%, var(--globe-deep) 100%);
  }
  .globe-reflection {
    position: absolute; left: 617px; top: 630px; width: 187px; height: 90px; border-radius: 50% 50% 0 0;
    background: linear-gradient(to bottom, rgba(140, 195, 230, 0.45), rgba(255, 255, 255, 0));
  }
  .content-panel {
    position: absolute; left: 75px; top: 77px; width: 783px; height: 354px;
    background: var(--panel); border-radius: 10px; padding: 16px 20px 0 20px;
    color: var(--text);
  }
  .subheading {
    font-family: "Open Sans", sans-serif; font-weight: 400;
    font-size: 35px; letter-spacing: 0.3px; line-height: 1; margin-bottom: 40px;
  }
  .body-copy p {
    font-family: "Questrial", sans-serif; font-size: 13.6px; line-height: 17.2px;
    letter-spacing: 0.45px; -webkit-text-stroke: 0.25px var(--text);
    white-space: nowrap; margin-bottom: 17px;
  }
</style>
</head>
<body>
<div class="canvas">
  <section class="page">
    <div class="wave-artwork" role="img" aria-label="Decorative flowing red and blue ribbon waves over a white ground"></div>
    <div class="globe-artwork" role="img" aria-label="Glossy globe illustration"></div>
    <div class="globe-reflection" role="img" aria-label="Faint reflection of the globe"></div>

    <article class="content-panel">
      <h2 class="subheading">SUBHEADING</h2>
      <div class="body-copy">
        <p>"Lorem ipsum dolor sit amet, consectetur adipisicing elit, sed do eiusmod tempor incididunt ut labore et dolore<br>magna aliqua. Ut enim ad minim veniam, quis nostrud exercitation ullamco laboris nisi ut aliquip ex ea commodo<br>consequat. Duis aute irure dolor in reprehenderit in voluptate velit esse cillum dolore eu fugiat nulla pariatur.</p>
        <p>Excepteur sint occaecat cupidatat non proident, sunt in culpa qui officia deserunt mollit anim id est laborum."<br>&nbsp;"At vero eos et accusamus et iusto odio dignissimos ducimus qui blanditiis praesentium voluptatum deleniti atque<br>corrupti quos dolores et quas molestias excepturi sint occaecati cupiditate non provident, similique sunt in culpa<br>qui officia deserunt mollitia animi, id est laborum et dolorum fuga.</p>
        <p>Et harum quidem rerum facilis est et expedita distinctio. Nam libero tempore, cum soluta nobis est eligendi optio<br>cumque nihil impedit quo minus id quod maxime placeat facere possimus, omnis voluptas assumenda est, omnis<br>dolor repellendus. Temporibus autem quibusdam et aut officiis debitis aut rerum necessitatibus saepe eveniet ut<br>et voluptates repudiandae sint et molestiae non recusandae. Itaque earum rerum hic tenetur a sapiente delec-<br>tus, ut aut reiciendis voluptatibus maiores alias consequatur aut perferendis doloribus asperiores repellat."</p>
      </div>
    </article>
  </section>
</div>
</body>
</html>
```